business card deign

Logo needs the following on it.
1. attached logo
2. Tagline - "If it keeps a drink cold or the party going...we do it!"
3. Name- Dalton Pikes, Founder and CPO
4. Address - 412 E. Carver Avenue, Ste 2207, Tampa, FL. 33917
5. Phone - 555.318.4726

```html
<!DOCTYPE html>
<html lang="en">
<head>
<meta charset="utf-8">
<title>Hopwell Business Card</title>
<link rel="stylesheet" href="https://fonts.googleapis.com/css2?family=Roboto+Condensed:wght@700&family=Arimo:wght@400&display=swap">
<style>
  :root {
    --backdrop: #3a3b3c;
    --card-dark: #232323;
    --card-dark-mark: #303030;
    --card-light: #ffffff;
    --ink: #111111;
  }
  * { margin: 0; padding: 0; box-sizing: border-box; }
  html, body { width: 900px; height: 1200px; overflow: hidden; }
  body { background: var(--backdrop); position: relative; font-family: "Arimo", Arial, sans-serif; }

  .card {
    position: absolute;
    left: 135px;
    width: 630px;
    height: 358px;
  }
  .card--front { top: 215px; background: var(--card-dark); }
  .card--back { top: 629px; background: var(--card-light); color: var(--ink); }

  .front-mark {
    position: absolute;
    left: 0; right: 0; top: 150px;
    text-align: center;
    font-family: "Roboto Condensed", Arial, sans-serif;
    font-weight: 700;
    font-size: 44px;
    letter-spacing: 14px;
    color: var(--card-dark-mark);
  }

  .brand {
    position: absolute;
    left: 120px;
    top: 100px;
    width: 196px;
    text-align: center;
  }
  .brand__square {
    width: 58px; height: 58px;
    background: var(--ink);
    margin: 20px auto 34px;
  }
  .brand__name {
    font-family: "Roboto Condensed", Arial, sans-serif;
    font-weight: 700;
    font-size: 30px;
    letter-spacing: 11px;
    margin-right: -11px;
    line-height: 1;
  }

  .divider {
    position: absolute;
    left: 341px; top: 98px;
    width: 2px; height: 164px;
    background: var(--ink);
  }

  .contact { position: absolute; left: 368px; top: 106px; }
  .contact__name {
    font-family: "Roboto Condensed", Arial, sans-serif;
    font-weight: 700;
    font-size: 29px;
    line-height: 1;
    letter-spacing: 0.2px;
  }
  .contact__title { font-size: 14.5px; margin-top: 11px; }
  .contact__phone {
    font-size: 17px; margin-top: 18px; letter-spacing: 0.8px;
    display: flex; align-items: center; gap: 6px;
  }
  .contact__phone svg { width: 12px; height: 12px; }
  .contact__address { font-size: 14px; line-height: 25px; margin-top: 9px; }

  .tagline {
    position: absolute;
    left: 0; right: 0; top: 303px;
    text-align: center;
    font-family: "Roboto Condensed", Arial, sans-serif;
    font-weight: 700;
    font-size: 16px;
    letter-spacing: 0.6px;
  }
</style>
</head>
<body>
  <section class="card card--front">
    <div class="front-mark">HOPWELL</div>
  </section>

  <section class="card card--back">
    <div class="brand">
      <div class="brand__square"></div>
      <div class="brand__name">HOPWELL</div>
    </div>

    <div class="divider"></div>

    <div class="contact">
      <div class="contact__name">DALTON PIKES</div>
      <div class="contact__title">Founder and CPO</div>
      <div class="contact__phone">
        <svg viewBox="0 0 24 24" aria-hidden="true"><path fill="#111" d="M6.6 10.8c1.4 2.8 3.8 5.1 6.6 6.6l2.2-2.2c.3-.3.7-.4 1-.2 1.1.4 2.3.6 3.6.6.6 0 1 .4 1 1V20c0 .6-.4 1-1 1C10.6 21 3 13.4 3 4c0-.6.4-1 1-1h3.5c.6 0 1 .4 1 1 0 1.3.2 2.5.6 3.6.1.3 0 .7-.2 1l-2.3 2.2z"/></svg>
        <span>555.318.4726</span>
      </div>
      <div class="contact__address">
        412 E. Carver Avenue, Ste 2207<br>
        Tampa, FL. 33917
      </div>
    </div>

    <p class="tagline">If it keeps a drink cold or the party going...we do it!</p>
  </section>
</body>
</html>
```